6"x9" Postcard Mailer

A 6"x9" Postcard mailer targeted to forensic laboratories to advertise or mock forensic samples (https://veltrascience.example/products/mock-forensic-samples/).

Here is some copy, but we can modify if there is not enough space:

Headline:
Expedite Training, Validation, & R&D with Our Ready-to-Use Mock Samples

Bullet Points:

- Wide Variety of Sample Types: IRB-approved samples mimicking crime scene substances, including semen, hair, bone, saliva, blood, and vaginal epithelial cells.
- Diverse Scenarios: Simulate sexual assault and degraded samples for varied conditions.
- Custom Solutions: Tailored DNA quantities and concentrations to suit your lab's needs.

Use discount code TRAL47 for a 10% discount

```html
<!DOCTYPE html>
<html lang="en">
<head>
<meta charset="utf-8">
<title>Veltra Science Mock Samples Postcard</title>
<link rel="stylesheet" href="https://fonts.googleapis.com/css2?family=Arimo:wght@400;700&display=swap">
<style>
:root{
  --board:#c9c9c9;
  --label:#3a3a3a;
  --ink-black:#05070d;
  --navy:#0a1a4a;
  --navy-deep:#050d2c;
  --blue:#2f6fd0;
  --blue-bright:#2a7ee0;
  --blue-soft:#3d8ee6;
  --cyan:#29b6f0;
  --orange:#f39a1f;
  --orange-deep:#e8781a;
  --white:#ffffff;
  --mail:#f1eff0;
}
*{margin:0;padding:0;box-sizing:border-box}
html,body{width:1200px;height:1200px;overflow:hidden}
body{background:var(--board);font-family:"Arimo",Arial,sans-serif;position:relative}
.side-label{position:absolute;font-size:31px;color:var(--label);letter-spacing:1px}
.side-label.front{left:109px;top:310px}
.side-label.back{left:970px;top:820px}

.card{position:absolute;left:258px;width:675px;overflow:hidden}
.card-front{top:73px;height:455px;background:var(--ink-black)}
.card-back{top:584px;height:530px;background:linear-gradient(120deg,var(--navy-deep) 0%,var(--navy) 45%,#0f3690 100%)}

.photo{position:absolute}
.front-photo{inset:0;background:
  radial-gradient(ellipse at 78% 88%,#f4f0f0 0%,#d9d6da 30%,transparent 60%),
  radial-gradient(ellipse at 45% 35%,#2b56c9 0%,#1a3a9a 25%,transparent 55%),
  radial-gradient(ellipse at 85% 25%,#8e8e94 0%,#3a3a40 35%,transparent 65%),
  linear-gradient(180deg,#06080f 0%,#0d1530 55%,#c9c5c9 100%)}
.molecule-photo{left:300px;top:0;right:0;bottom:0;background:
  radial-gradient(circle at 70% 40%,rgba(40,140,240,.55) 0%,transparent 45%),
  radial-gradient(circle at 85% 75%,rgba(30,110,220,.45) 0%,transparent 40%)}
.product-photo{left:37px;top:314px;width:301px;height:201px;background:
  radial-gradient(ellipse at 50% 60%,#e8eef8 0%,#9fb3d8 35%,#1a3a8a 70%,transparent 80%)}

.front-decor,.back-decor,.mail-area{position:absolute;left:0;top:0}

.brand{position:absolute;color:var(--white)}
.brand-name{display:flex;align-items:center;gap:10px;font-weight:700;font-size:36px;letter-spacing:-.5px;line-height:1}
.brand-dot{width:14px;height:14px;border-radius:50%;background:var(--blue-soft)}
.brand-tag{font-size:11px;letter-spacing:3.2px;margin-top:8px;font-weight:400}
.card-front .brand{left:39px;top:30px}
.card-back .brand{left:51px;top:48px}

.headline{position:absolute;left:29px;top:238px;color:var(--white);font-weight:700;font-size:32px;line-height:31px;letter-spacing:-.3px}

.offer{position:absolute;right:33px;top:50px;text-align:right;color:var(--white)}
.offer-main{font-weight:700;font-size:46px;line-height:1;letter-spacing:-1.5px}
.offer-main .pct{color:var(--orange)}
.offer-main sup{font-size:22px;vertical-align:top;position:relative;top:2px;margin-right:4px}
.offer-code{display:flex;align-items:center;justify-content:flex-end;gap:6px;margin-top:4px}
.offer-code-label{font-weight:700;font-size:16px}
.code-pill{background:linear-gradient(180deg,var(--orange),var(--orange-deep));border-radius:13px;padding:2px 14px;font-weight:700;font-size:20px;letter-spacing:.5px}

.features{position:absolute;left:44px;top:121px;width:330px}
.feature{display:flex;gap:10px;position:relative}
.feature-icon{flex:0 0 54px;height:54px;border:1.5px solid var(--white);border-radius:50%;display:flex;align-items:center;justify-content:center}
.feature-text{color:var(--white)}
.feature-title{color:var(--cyan);font-weight:700;font-size:14px;margin-bottom:2px}
.feature-body{font-size:12px;line-height:15px}
.feature-1{margin-top:0}
.feature-2{margin-top:17px}
.feature-3{margin-top:13px}
.connector{position:absolute;left:71px;width:1.5px;background:var(--white)}
</style>
</head>
<body>

<div class="side-label front">FRONT</div>
<div class="side-label back">BACK</div>

<section class="card card-front">
  <div class="photo front-photo" role="img" aria-label="Gloved forensic scientist swabbing blood droplets on a white surface beside a ring, with a glowing DNA helix in the dark background"></div>
  <svg class="front-decor" width="675" height="455" viewBox="0 0 675 455">
    <defs>
      <linearGradient id="blobBlue" x1="0" y1="1" x2="1" y2="0">
        <stop offset="0" stop-color="#2b5fb8"/>
        <stop offset="1" stop-color="#2a8fdc"/>
      </linearGradient>
    </defs>
    <circle cx="428" cy="0" r="32" fill="#2a2a30" opacity=".7"/>
    <circle cx="518" cy="14" r="82" fill="#2f6fd6"/>
    <circle cx="582" cy="65" r="34" fill="#ffffff" opacity=".25"/>
    <path d="M0 195 C60 175 150 175 195 215 C215 235 192 265 215 290 C255 320 292 390 300 455 L0 455 Z" fill="url(#blobBlue)"/>
  </svg>
  <div class="brand">
    <div class="brand-name"><span class="brand-dot"></span>Veltra Science</div>
    <div class="brand-tag">SCIENCE IN EVERY SAMPLE</div>
  </div>
  <h1 class="headline">Expedite<br>Training<br>Validation,<br>&amp; R&amp;D with Our<br>Ready-to-Use<br>Mock Samples</h1>
</section>

<section class="card card-back">
  <div class="photo molecule-photo" role="img" aria-label="Glowing blue molecular structure with floating bubbles"></div>
  <svg class="back-decor" width="675" height="530" viewBox="0 0 675 530">
    <circle cx="230" cy="-10" r="40" fill="#0d2260" opacity=".8"/>
    <circle cx="340" cy="0" r="92" fill="#2f6fd6"/>
    <circle cx="410" cy="35" r="48" fill="#ffffff" opacity=".2"/>
  </svg>
  <div class="photo product-photo" role="img" aria-label="Two white and blue kit boxes, one open showing sample vials"></div>

  <div class="brand">
    <div class="brand-name"><span class="brand-dot"></span>Veltra Science</div>
    <div class="brand-tag">SCIENCE IN EVERY SAMPLE</div>
  </div>

  <div class="offer">
    <div class="offer-main"><span class="pct">10<sup>%</sup></span>discount</div>
    <div class="offer-code"><span class="offer-code-label">discount code</span><span class="code-pill">TRAL47</span></div>
  </div>

  <div class="connector" style="top:175px;height:15px"></div>
  <div class="connector" style="top:245px;height:13px"></div>

  <div class="features">
    <div class="feature feature-1">
      <div class="feature-icon">
        <svg width="30" height="30" viewBox="0 0 30 30" fill="none" stroke="#fff" stroke-width="1.3">
          <path d="M10 6 L15 3 L20 6 L20 12 L15 15 L10 12 Z"/>
          <path d="M15 15 L20 18 L20 24 L15 27 L10 24 L10 18 Z"/>
          <path d="M20 12 L25 9 M10 18 L5 15 M15 27 L12 29"/>
        </svg>
      </div>
      <div class="feature-text">
        <div class="feature-title">Wide Variety of Sample Types:</div>
        <div class="feature-body">IRB-approved samples mimicking crime scene substances, including semen, hair, bone, saliva, blood, and vaginal epithelial cells.</div>
      </div>
    </div>
    <div class="feature feature-2">
      <div class="feature-icon">
        <svg width="30" height="30" viewBox="0 0 30 30" fill="none" stroke="#fff" stroke-width="1.3">
          <rect x="4" y="6" width="22" height="15" rx="1"/>
          <path d="M15 21 L15 25 M10 25 L20 25"/>
          <path d="M15 9 L19 11 L19 16 L15 18 L11 16 L11 11 Z"/>
        </svg>
      </div>
      <div class="feature-text">
        <div class="feature-title">Diverse Scenarios:</div>
        <div class="feature-body">Simulate sexual assault and degraded samples for varied conditions.</div>
      </div>
    </div>
    <div class="feature feature-3">
      <div class="feature-icon">
        <svg width="30" height="30" viewBox="0 0 30 30" fill="none" stroke="#fff" stroke-width="1.3">
          <path d="M6 4 C14 10 6 20 14 26 M14 4 C6 10 14 20 6 26"/>
          <path d="M7 9 L13 9 M7 21 L13 21"/>
          <circle cx="22" cy="15" r="5"/>
          <circle cx="22" cy="15" r="1.5"/>
        </svg>
      </div>
      <div class="feature-text">
        <div class="feature-title">Custom Solutions:</div>
        <div class="feature-body">Tailored DNA quantities and concentrations to suit your lab's needs.</div>
      </div>
    </div>
  </div>

  <svg class="mail-area" width="675" height="530" viewBox="0 0 675 530" aria-hidden="true">
    <polygon points="535,270 675,270 675,530 354,530 354,460 535,460" fill="var(--mail)"/>
  </svg>
</section>

</body>
</html>
```